maplecrest gymnastics academy

need a website for above to contain information about the academy, enrollment form etc..

Need a web design for new business Maplecrest Gymnastics Academy offering classes in gymnastics. Info on the business is in the doc called "Web design" which details the tabs I will need on my page. Please see our Facebook page to get an idea of the style Maplecrestgymnasticsacademy.

Thank you for your help. I do not require hosting of a domain name just need it all ready to be hosted. Thanks

Budget now increased to include the coding of the website as well.

```html
<!DOCTYPE html>
<html lang="en">
<head>
<meta charset="utf-8">
<title>Maplecrest Gymnastics Academy</title>
<link rel="stylesheet" href="https://fonts.googleapis.com/css2?family=Varela+Round&family=Open+Sans:wght@400;600&display=swap">
<style>
:root{
  --gold-top:#b8a660;
  --gold-mid:#a89448;
  --gold-dark:#8f7c35;
  --nav-band:#ebe2a2;
  --accent:#d3c200;
  --accent-light:#e9e08c;
  --olive:#b2a35d;
  --ink:#222;
  --text:#555;
  --muted:#777;
  --black:#000;
  --panel:#222;
  --white:#fff;
}
*{margin:0;padding:0;box-sizing:border-box}
html,body{width:992px;height:1200px;overflow:hidden;background:var(--white)}
body{position:relative;font-family:"Open Sans",sans-serif;color:var(--text)}
.heading-font{font-family:"Varela Round",sans-serif}
.abs{position:absolute}

/* header */
.top-band{left:0;top:0;width:992px;height:62px;background:linear-gradient(var(--gold-top),var(--gold-mid))}
.nav-band{left:0;top:62px;width:992px;height:40px;background:var(--nav-band)}
.brand{left:132px;top:12px;width:95px;height:104px;background:var(--accent);border:3px solid #3a3a2a;border-radius:8px;display:flex;align-items:center;justify-content:center;text-align:center;padding:6px;font-family:"Varela Round",sans-serif;font-size:13px;line-height:1.25;color:#111;z-index:3}
.phone{left:724px;top:30px;display:flex;align-items:center;gap:6px;font-family:"Varela Round",sans-serif;font-size:17px;color:var(--white)}
.nav{left:362px;top:62px;height:40px;display:flex;list-style:none}
.nav li{height:40px;display:flex;align-items:center;padding:0 20px;font-family:"Varela Round",sans-serif;font-size:13px;color:#111;border-right:1px solid #cfc27c}
.nav li:last-child{border-right:none}

/* hero */
.hero{left:0;top:102px;width:992px;height:414px;background:radial-gradient(ellipse 60% 40% at 50% 115%,#8a7a1a 0%,#2a2406 55%,var(--black) 80%),var(--black)}
.hero-photo{left:430px;top:13px;width:428px;height:343px;background:radial-gradient(circle at 60% 45%,#7a1a1a 0%,#3a1414 30%,#141826 70%,#0a0c14 100%)}
.hero-title{left:135px;top:114px;font-size:31px;color:var(--accent);font-family:"Varela Round",sans-serif}
.hero-sub{left:135px;top:153px;font-size:19px;color:var(--white);font-family:"Varela Round",sans-serif}
.hero-copy{left:133px;top:184px;width:350px;font-size:11px;line-height:17px;color:#aaa}
.btn{left:132px;top:227px;width:96px;height:27px;background:var(--accent);color:var(--white);font-size:11px;font-weight:600;display:flex;align-items:center;justify-content:center;font-family:"Varela Round",sans-serif}

/* feature boxes */
.features{left:132px;top:458px;width:724px;height:120px;display:flex;z-index:2}
.feature{width:241px;height:120px;padding:20px 20px 0;border-bottom:6px solid var(--accent);background:var(--black);border-top:1px solid #333}
.feature:nth-child(2){background:var(--panel);border-bottom-color:var(--accent-light)}
.feature:nth-child(3){border-bottom-color:var(--olive)}
.feature h3{font-family:"Varela Round",sans-serif;font-weight:400;font-size:17px;color:var(--white);margin-bottom:4px}
.feature p{font-size:9px;line-height:14px;color:#ddd}
.feature a{display:block;margin-top:3px;font-size:10px;font-weight:600;color:var(--accent);text-decoration:none}

/* welcome */
.welcome{left:132px;top:617px;width:485px}
.welcome h2{font-family:"Varela Round",sans-serif;font-weight:400;font-size:19px;color:#333;margin-bottom:10px}
.welcome p{font-size:9.5px;line-height:15.5px;margin-bottom:7px}
.cards{left:132px;top:763px;width:485px;display:flex;gap:8px}
.card{width:156px}
.card-img{width:156px;height:79px}
.card h4{font-family:"Varela Round",sans-serif;font-weight:400;font-size:15px;color:var(--accent);margin:8px 0 3px -1px}
.card p{font-size:8.5px;line-height:14px;color:var(--muted)}

/* news */
.news{left:637px;top:616px;width:220px}
.news h2{font-family:"Varela Round",sans-serif;font-weight:400;font-size:18px;color:#333;margin-bottom:9px}
.post{display:flex;gap:10px;padding-bottom:12px;margin-bottom:16px;border-bottom:1px solid #ddd;height:76px}
.post:last-child{border-bottom:none}
.post-img{width:66px;height:54px;flex:none;margin-left:2px}
.post h5{font-family:"Varela Round",sans-serif;font-weight:400;font-size:11.5px;color:#b8a800;margin-bottom:2px}
.post p{font-size:8.5px;line-height:14px;color:#888}
.post a{font-size:10px;color:#222;text-decoration:none;display:block;margin-top:4px}

/* footer */
.footer{left:0;top:965px;width:992px;height:190px;background:linear-gradient(var(--olive),var(--gold-dark))}
.foot-col{top:30px;height:95px;font-size:11px;line-height:20px;color:#fff7d6}
.foot-col h6{font-family:"Varela Round",sans-serif;font-weight:400;font-size:16px;color:var(--white);margin-bottom:1px;line-height:22px}
.foot-col.sep{border-right:1px solid #c6b979}
.social{display:flex;gap:4px;margin-top:6px}
.social span{width:20px;height:20px;border-radius:50%;background:#f2ecd0;display:block}
.bottom-bar{left:0;top:1155px;width:992px;height:45px;background:var(--gold-dark);font-size:9px;color:#d7cc9c;padding:24px 0 0 152px}
</style>
</head>
<body>

<header>
  <div class="abs top-band"></div>
  <div class="abs nav-band"></div>
  <div class="abs brand">Maplecrest Gymnastics Academy</div>
  <div class="abs phone">
    <svg width="22" height="22" viewBox="0 0 22 22" aria-hidden="true"><circle cx="11" cy="11" r="9.5" fill="none" stroke="#111" stroke-width="1.6"/><path d="M7.5 6.5c.6-.6 1.4-.5 1.7.1l.8 1.6c.2.5 0 1-.4 1.3l-.5.4c.6 1.3 1.6 2.3 2.9 2.9l.4-.5c.3-.4.8-.6 1.3-.4l1.6.8c.6.3.7 1.1.1 1.7-1 1-2.6 1.1-3.8.3-1.8-1.1-3.3-2.6-4.4-4.4-.8-1.2-.7-2.8.3-3.8z" fill="#111"/></svg>
    555.014.2736
  </div>
  <ul class="abs nav">
    <li>HOME</li><li>ABOUT US</li><li>FORMS</li><li>MORE INFO</li><li>POLICIES</li>
  </ul>
</header>

<section class="abs hero">
  <div class="abs hero-photo" role="img" aria-label="Gymnast in a red leotard mid-leap in a split jump over a dark arena crowd"></div>
  <div class="abs hero-title">Mauris lacus vitae felisa</div>
  <div class="abs hero-sub">Etiam venenatis tristique imperdiet</div>
  <p class="abs hero-copy">Curabitur iaculis tempus eros Curabitur vel mi sit amet magna malesuada ultrices Ut nisi erat fermentum vel congue euismod</p>
  <div class="abs btn">LEARN MORE</div>
</section>

<section class="abs features">
  <div class="feature"><h3>Our Classes</h3><p>Curabitur iaculis tempus eros<br>Curabitur vel mi sit amet magna<br>malesuada ultrices nisi</p><a href="#">CLICK HERE</a></div>
  <div class="feature"><h3>Join Us Now</h3><p>Curabitur iaculis tempus eros<br>Curabitur vel mi sit amet magna<br>malesuada ultrices nisi</p><a href="#">CLICK HERE</a></div>
  <div class="feature"><h3>Why Gymnastics</h3><p>Curabitur iaculis tempus eros<br>Curabitur vel mi sit amet magna<br>malesuada ultrices nisi</p><a href="#">CLICK HERE</a></div>
</section>

<section class="abs welcome">
  <h2>Welcome to Maplecrest Gymnastics Academy</h2>
  <p>Gymnastics is for everyone, people&nbsp; of all ages, shapes, sizes and capabilities can participate in and enjoy gymnastics, We offer classes from Kindergym to Adult classes MGA is GYMSTATE Affiliated club and our coaches are accredited and qualified with National Gymnastics Council.</p>
  <p>MGA is newly established family business whose mission is to provide high quality gymnastics program in a wide variety activrities to suit all ages, levels and ability.</p>
</section>

<section class="abs cards">
  <div class="card">
    <div class="card-img" role="img" aria-label="Gymnast in a purple leotard performing a floor routine" style="background:linear-gradient(160deg,#2a2a5a,#6a3a9a 50%,#1e2040)"></div>
    <h4>About Our Training</h4>
    <p>Curabitur iaculis tempus eros Curabitur vel mi sit amet magna malesuada ultrices Ut nisi erat fermentum con</p>
  </div>
  <div class="card">
    <div class="card-img" role="img" aria-label="Gymnast in a blue leotard balancing on the beam" style="background:linear-gradient(160deg,#1a2438,#3a4a8a 55%,#2a2a30)"></div>
    <h4>Why Choose Us</h4>
    <p>Curabitur iaculis tempus eros Curabitur vel mi sit amet magna malesuada ultrices Ut nisi erat fermentum con</p>
  </div>
  <div class="card">
    <div class="card-img" role="img" aria-label="Gymnast in red performing a move on the balance beam" style="background:linear-gradient(170deg,#3a2a24,#a0302a 40%,#8a6a48 75%,#3a3028)"></div>
    <h4>Our Resources</h4>
    <p>Curabitur iaculis tempus eros Curabitur vel mi sit amet magna malesuada ultrices Ut nisi erat fermentum con</p>
  </div>
</section>

<aside class="abs news">
  <h2>News &amp; Blog Post</h2>
  <div class="post">
    <div class="post-img" role="img" aria-label="Gymnast in blue stretching on the mat" style="background:linear-gradient(150deg,#c8a888,#3a4a7a 60%,#a03030)"></div>
    <div><h5>Morbi ornare gravida</h5><p>Integer congue augue et malesuada iaculis ipsum dui aliquet felis at</p><a href="#">Read More</a></div>
  </div>
  <div class="post">
    <div class="post-img" role="img" aria-label="Gymnast in a pink leotard on the bars" style="background:linear-gradient(150deg,#2a2a4a,#b03a7a 55%,#3a3a5a)"></div>
    <div><h5>Morbi ornare gravida</h5><p>Integer congue augue et malesuada iaculis ipsum dui aliquet felis at</p><a href="#">Read More</a></div>
  </div>
  <div class="post">
    <div class="post-img" role="img" aria-label="Gymnast raising an arm under arena lights" style="background:linear-gradient(150deg,#4a5a8a,#2a2a4a 50%,#5a3a7a)"></div>
    <div><h5>Morbi ornare gravida</h5><p>Integer congue augue et malesuada iaculis ipsum dui aliquet felis at</p><a href="#">Read More</a></div>
  </div>
</aside>

<footer class="abs footer">
  <div class="abs foot-col sep" style="left:158px;width:89px"><h6>Company</h6>Home<br>About Us<br>Our Mission</div>
  <div class="abs foot-col sep" style="left:278px;width:102px"><h6>Sublinks</h6>Enrollment Form<br>Booking Form<br>Payment NOw</div>
  <div class="abs foot-col sep" style="left:405px;width:95px;height:95px"><h6>Resources</h6>General info<br>Timetable<br>Classes<br>News &amp; Events</div>
  <div class="abs foot-col sep" style="left:532px;width:99px"><h6>Support</h6>Term of Policies<br>Employment<br>Contact Us</div>
  <div class="abs foot-col" style="left:660px;width:180px"><h6>Get in touch</h6><span style="font-size:9px">Please connect with us on followings.</span>
    <div class="social"><span></span><span></span><span></span><span></span></div>
  </div>
</footer>
<div class="abs bottom-bar">© 2014 Company Name&nbsp; All right reserved&nbsp; Term of Use</div>

</body>
</html>
```